Sell the dream! Property investment proposal document

We are looking for a proposal document which outlines our vision for property development. The purpose of the document is to raise investment from investors - sell the dream!
Brief summary:
Kestrel Dwellings Developments, is an emerging New Zealand property investment company with a focus on providing unique property investment opportunities.
Our expertise and capabilities in architectural modular homes provide us with a remarkable advantage in tackling the development of properties that are typically considered challenging, remote, or uniquely positioned.
Our specialization in this niche sector of property development not only sets us apart from competitors, but also paves the way for lucrative investment opportunities in the New Zealand property market.
Feel free to use any images from www.kestreldwellings.co.nz
Target Market(s)
investors for a unique property development opportunity
Industry/Entity Type
luxury property development in unique locations throughout New Zealand
Colors
Designer to choose only greyscale colors for use in the design.
Look and feel

```html
<!DOCTYPE html>
<html lang="en">
<head>
<meta charset="utf-8">
<title>Kestrel Dwellings Developments – Investment Proposal</title>
<link href="https://fonts.googleapis.com/css2?family=Montserrat:wght@400;500;700&display=swap" rel="stylesheet">
<style>
  :root {
    --backdrop: #7a7a7a;
    --paper: #ffffff;
    --ink: #2b2b2b;
    --ink-soft: #3a3a3a;
    --footer: #2a2829;
    --footer-text: #ffffff;
  }
  * { margin: 0; padding: 0; box-sizing: border-box; }
  html, body {
    width: 1200px; height: 650px; overflow: hidden;
    background: var(--backdrop);
    font-family: "Montserrat", sans-serif;
    color: var(--ink);
  }
  .spread { position: relative; width: 1200px; height: 650px; }
  .page {
    position: absolute; top: 90px; width: 342px; height: 470px;
    background: var(--paper); overflow: hidden;
    box-shadow: 0 6px 28px rgba(0,0,0,0.45);
  }
  .page--cover { left: 70px; }
  .page--overview { left: 429px; }
  .page--advantage { left: 788px; }

  .cover-scene {
    position: absolute; inset: 0 0 19px 0;
    background:
      linear-gradient(180deg, #dfe9f8 0%, #f3f6fb 45%, #dfe3e6 62%, #3d3d3d 66%, #3a3a3a 72%, #9aa6ad 74%, #6f7d5a 80%, #7fa14a 88%, #8fb552 100%);
  }
  .cover-title { position: absolute; top: 0; left: 0; width: 100%; text-align: center; z-index: 1; }
  .brand-name {
    position: absolute; top: 36px; width: 100%;
    font-size: 56px; line-height: 62px; font-weight: 500; letter-spacing: -1px; color: var(--ink);
  }
  .cover-subtitle {
    position: absolute; top: 109px; width: 100%;
    font-size: 17px; line-height: 22px; font-weight: 400; color: var(--ink-soft);
  }
  .cover-date {
    position: absolute; top: 141px; width: 100%;
    font-size: 17px; line-height: 22px; font-weight: 700; color: var(--ink);
  }
  .cover-version {
    position: absolute; top: 176px; width: 100%;
    font-size: 10px; line-height: 14px; font-weight: 400; color: var(--ink);
  }

  .section { position: absolute; left: 16px; right: 17px; z-index: 1; }
  .section h2 {
    font-size: 12px; line-height: 14px; font-weight: 500; letter-spacing: 0.1px; color: var(--ink);
    margin-bottom: 9px; white-space: nowrap;
  }
  .section p {
    font-size: 5.3px; line-height: 10.2px; letter-spacing: -0.02px;
    text-align: justify; color: var(--ink-soft);
  }

  .interior-photo {
    position: absolute; left: 0; right: 0; top: 311px; height: 140px;
    background: linear-gradient(180deg, #ffffff 0%, #dfe8f0 20%, #a9bfd2 45%, #6b7f90 62%, #2d2c2e 78%, #1f1c1d 100%);
  }
  .seaside-photo {
    position: absolute; left: 0; right: 0; top: 244px; height: 207px;
    background: linear-gradient(180deg, #ffffff 0%, #e9e6e1 10%, #b9b5ae 20%, #6f7276 32%, #bfae90 50%, #d3c4a6 62%, #8c8377 76%, #6d655d 100%);
  }

  .page-footer {
    position: absolute; left: 0; right: 0; bottom: 0; height: 19px;
    background: var(--footer); color: var(--footer-text);
    display: flex; align-items: center; justify-content: space-between;
    padding: 0 9px 0 8px; z-index: 2;
  }
  .page-footer .email { font-size: 8.5px; font-weight: 400; }
  .page-number {
    width: 15px; height: 15px; border-radius: 50%;
    background: var(--paper); color: var(--footer);
    font-size: 6px; font-weight: 700;
    display: flex; align-items: center; justify-content: center;
  }
</style>
</head>
<body>
<div class="spread">

  <section class="page page--cover">
    <div class="cover-scene" role="img" aria-label="Photograph of a dark cantilevered modular home on a grassy rocky hillside above the sea under a pale sky"></div>
    <div class="cover-title">
      <div class="brand-name">Kestrel</div>
      <div class="cover-subtitle">Kestrel Dwellings Developments</div>
      <div class="cover-date">MAY 29,2024</div>
      <div class="cover-version">Version:01</div>
    </div>
    <footer class="page-footer"><span class="email">info@kestreldwellings.com</span><span class="page-number">01</span></footer>
  </section>

  <section class="page page--overview">
    <div class="interior-photo" role="img" aria-label="Photograph of lounge chairs in a glass-walled living room overlooking the ocean"></div>
    <div class="section" style="top:16px;">
      <h2>BUSINESS OVERVIEW</h2>
      <p>Kestrel Dwellings Developments, is an emerging New Zealand property investment company with a focus on providing unique property investment opportunities.Our expertise and capabilities in architectural modular homes provide us with a remarkable advantage in tackling the development of properties that are typically considered challenging, remote, or uniquely positioned. As a company, with 48 employees boasting a wealth of experience in handling complex architectural projects, making us well-equipped to navigate the intricacies and demands of such ventures. This advantage allows us to not only execute projects efficiently but also to deliver exceptional results within condensed time frames. By capitalizing on our ability to develop difficult, remote, or one-of-a-kind properties swiftly and effectively, Kestrel Dwellings Developments offers investors a rare chance to engage in projects that promise exceptional profitability in the New Zealand property market. Our specialization in this niche sector of property development not only sets us apart from competitors, but also paves the way for lucrative investment opportunities in the New Zealand property market.</p>
    </div>
    <div class="section" style="top:164px;">
      <h2>BUSINESS ORIGINS</h2>
      <p>Kestrel Dwellings Developments was established with the goal of transforming the property investment market in New Zealand by introducing an innovative approach that centers on architectural modular designs and streamlined project timelines. Driven by our enthusiasm for architecture and real estate, we have expanded our successful business model to not only offer financial opportunities for investors but also to expand on our passion for high-end architectural design. With a wealth of experience accumulated over the past six years in the construction and the property market, we are pivoting to focus solely on our property development initiatives, presenting completed Kestrel projects to the market, in exclusive locations. These projects will boast high-quality standards, meticulous attention to detail and landscaping, and creative design elements. By introducing completed Kestrel properties into the market, we aim to reach a wider audience, catering to individuals who prefer ready-to-occupy homes, over engaging in the design and construction process. This approach also simplifies the financing process for prospective buyers, as established properties are often preferred by financial lenders</p>
    </div>
    <footer class="page-footer"><span class="email">info@kestreldwellings.com</span><span class="page-number">02</span></footer>
  </section>

  <section class="page page--advantage">
    <div class="seaside-photo" role="img" aria-label="Photograph of a glass pavilion home on a pebbled shore facing the sea at sunset"></div>
    <div class="section" style="top:16px;">
      <h2>COMPETITIVE ADVANTAGE</h2>
      <p>Our competitive advantage lies in the uniqueness of our property investment opportunities. Unlike traditional real estate companies, we focus on offering properties that are not only profitable but also aesthetically pleasing and unique. By catering to the tastes of architecture lovers, we set ourselves apart from the competition and attract a niche market of customers who appreciate the artistry and design of our projects. Additionally, the streamlined and condensed timelines facilitated by our modular approach provide quicker returns on investment</p>
    </div>
    <div class="section" style="top:117px;">
      <h2>FINANCIAL SUMMARY</h2>
      <p>In terms of financial projections, with each development, we anticipate a profit of 10%-20% which will be project dependent.This growth is fueled by the increasing demand for unique property investments in New Zealand and our ability to deliver high-quality services to the market in a condensed time frame, with heavily controlled costs. With a solid business model and a dedicated team, we are confident in our ability to achieve success and establish Kestrel Dwellings Investments as a trusted name in the industry. New Zealand's property market has been experiencing steady growth over the years, making it an attractive destination for property investors. With its beautiful landscapes and strong economy, New Zealand offers a diverse range of investment opportunities for both local and international investors. The demand for quality properties in prime locations continues to rise, creating a favorable environment for property investment companies like ours that can lean on our modular benefits of being able to reach unique and remote locations.</p>
    </div>
    <footer class="page-footer"><span class="email">info@kestreldwellings.com</span><span class="page-number">03</span></footer>
  </section>

</div>
</body>
</html>
```